Business card design for my company.
I would like the card's background colour to be black. You can also see our web site to get an idea of our brand. https://www.tmwhomecrafting.com.au/
- Name
- Email

```html
<!DOCTYPE html>
<html lang="en">
<head>
<meta charset="utf-8">
<title>TMW Home Crafting – Business Card</title>
<link href="https://fonts.googleapis.com/css2?family=Montserrat:wght@400;700&display=swap" rel="stylesheet">
<style>
  :root {
    --page-bg: #d9d9d6;
    --card-bg: #222222;
    --brand-green: #1f9a47;
    --text-white: #f4f4f4;
    --corner-white: #f7f7f7;
  }
  * { box-sizing: border-box; margin: 0; padding: 0; }
  html, body {
    width: 1200px;
    height: 912px;
    overflow: hidden;
    background: var(--page-bg);
    font-family: "Montserrat", Arial, sans-serif;
  }
  .canvas {
    width: 1200px;
    height: 912px;
    display: flex;
    flex-direction: column;
    align-items: center;
    justify-content: center;
    gap: 40px;
  }
  .card {
    position: relative;
    width: 700px;
    height: 400px;
    background: var(--card-bg);
    border-radius: 22px;
    overflow: hidden;
    box-shadow: 0 10px 24px rgba(0,0,0,0.25);
  }
  .brand {
    display: flex;
    align-items: center;
    gap: 14px;
    color: var(--text-white);
    font-weight: 700;
    text-transform: uppercase;
    letter-spacing: 0.12em;
  }
  .brand-square {
    background: var(--brand-green);
    flex: none;
  }
  /* front */
  .card-front {
    display: flex;
    align-items: center;
    justify-content: center;
  }
  .card-front .brand { font-size: 34px; }
  .card-front .brand-square { width: 30px; height: 30px; }
  /* back */
  .corner-cut {
    position: absolute;
    top: 0;
    right: 0;
  }
  .card-back .brand {
    position: absolute;
    left: 50px;
    top: 56px;
    font-size: 24px;
  }
  .card-back .brand-square { width: 22px; height: 22px; }
  .person {
    position: absolute;
    left: 50px;
    top: 150px;
  }
  .person-name {
    color: var(--brand-green);
    font-weight: 700;
    font-size: 32px;
    letter-spacing: 0.02em;
    text-transform: uppercase;
    line-height: 1.1;
  }
  .person-title {
    color: var(--text-white);
    font-size: 20px;
    margin-top: 4px;
  }
  .rule {
    width: 28px;
    height: 2px;
    background: var(--brand-green);
    margin: 22px 0 16px;
  }
  .contact-list { list-style: none; }
  .contact-item {
    display: flex;
    align-items: center;
    gap: 12px;
    color: var(--text-white);
    font-size: 19px;
    line-height: 1.65;
  }
  .contact-icon { width: 18px; height: 18px; flex: none; }
</style>
</head>
<body>
<main class="canvas">
  <section class="card card-front" aria-label="Card front">
    <div class="brand"><span class="brand-square"></span><span class="brand-name">TMW Home Crafting</span></div>
  </section>

  <section class="card card-back" aria-label="Card back">
    <svg class="corner-cut" width="300" height="140" viewBox="0 0 300 140" aria-hidden="true">
      <polygon points="90,0 300,0 300,40 110,40" fill="var(--corner-white)"/>
      <polyline points="0,140 110,40 300,40" fill="none" stroke="var(--brand-green)" stroke-width="9"/>
    </svg>

    <div class="brand"><span class="brand-square"></span><span class="brand-name">TMW Home Crafting</span></div>

    <div class="person">
      <h1 class="person-name">Darren Keller</h1>
      <p class="person-title">CEO/Founder</p>
      <div class="rule"></div>
      <ul class="contact-list">
        <li class="contact-item">
          <svg class="contact-icon" viewBox="0 0 24 24" aria-hidden="true"><path fill="var(--brand-green)" d="M6.6 10.8a15 15 0 0 0 6.6 6.6l2.2-2.2a1 1 0 0 1 1-.25 11.4 11.4 0 0 0 3.6.57 1 1 0 0 1 1 1V20a1 1 0 0 1-1 1A17 17 0 0 1 3 4a1 1 0 0 1 1-1h3.5a1 1 0 0 1 1 1c0 1.25.2 2.45.57 3.57a1 1 0 0 1-.25 1z"/></svg>
          555-214-0879
        </li>
        <li class="contact-item">
          <svg class="contact-icon" viewBox="0 0 24 24" aria-hidden="true"><rect x="2" y="5" width="20" height="14" fill="var(--brand-green)"/><polyline points="2,5 12,13 22,5" fill="none" stroke="var(--card-bg)" stroke-width="1.6"/></svg>
          info@tmwhomecrafting.com.au
        </li>
        <li class="contact-item">
          <svg class="contact-icon" viewBox="0 0 24 24" aria-hidden="true"><g fill="none" stroke="var(--brand-green)" stroke-width="1.8"><circle cx="12" cy="12" r="9.5"/><ellipse cx="12" cy="12" rx="4.5" ry="9.5"/><line x1="2.5" y1="12" x2="21.5" y2="12"/></g></svg>
          www.tmwhomecrafting.com.au
        </li>
      </ul>
    </div>
  </section>
</main>
</body>
</html>
```